The Linen Loft Co

We need a business card design for our wardrobe company.
Please visit our website www.gentlelinenlofts.com to get an idea of who we are.

```html
<!DOCTYPE html>
<html lang="en">
<head>
<meta charset="utf-8">
<title>The Linen Loft Co – Business Card</title>
<link href="https://fonts.googleapis.com/css2?family=Roboto:wght@400;500;700&display=swap" rel="stylesheet">
<style>
  :root {
    --backdrop: #262424;
    --card: #ffffff;
    --ink: #111111;
    --body: #3c3c3c;
    --muted: #a8a8a8;
  }
  * { margin: 0; padding: 0; box-sizing: border-box; }
  html, body {
    width: 1200px;
    height: 989px;
    overflow: hidden;
    background: var(--backdrop);
    font-family: "Roboto", Arial, sans-serif;
  }
  .card {
    position: absolute;
    left: 50px;
    top: 178px;
    width: 1100px;
    height: 634px;
    background: var(--card);
  }
  .brand {
    position: absolute;
    left: 535px;
    top: 86px;
    display: flex;
    align-items: center;
    gap: 22px;
  }
  .brand-mark {
    width: 78px;
    height: 78px;
    background: var(--ink);
  }
  .brand-text { color: var(--ink); }
  .brand-name {
    font-size: 25px;
    font-weight: 500;
    letter-spacing: 0.2px;
    text-transform: uppercase;
  }
  .brand-tagline {
    margin-top: 10px;
    font-size: 21px;
    font-weight: 500;
  }
  .person {
    position: absolute;
    left: 62px;
    top: 330px;
  }
  .person-name {
    font-size: 40px;
    font-weight: 700;
    color: var(--ink);
    line-height: 1.1;
  }
  .person-role {
    font-size: 27px;
    font-weight: 500;
    color: var(--muted);
    line-height: 1.2;
  }
  .contacts {
    position: absolute;
    left: 62px;
    top: 435px;
    list-style: none;
  }
  .contacts li {
    display: flex;
    align-items: center;
    gap: 12px;
    height: 34px;
    font-size: 26px;
    color: var(--body);
  }
  .contacts svg { width: 26px; height: 26px; flex: none; }
  .address {
    position: absolute;
    left: 60px;
    top: 550px;
    font-size: 26px;
    color: var(--body);
  }
</style>
</head>
<body>
  <main class="card">
    <div class="brand">
      <div class="brand-mark"></div>
      <div class="brand-text">
        <div class="brand-name">The Linen Loft Co</div>
        <div class="brand-tagline">Storage Made Simple</div>
      </div>
    </div>

    <div class="person">
      <div class="person-name">Daniel Harper</div>
      <div class="person-role">President</div>
    </div>

    <ul class="contacts">
      <li>
        <svg viewBox="0 0 24 24" aria-hidden="true"><path fill="#111" d="M6.6 10.8c1.4 2.8 3.8 5.1 6.6 6.6l2.2-2.2c.3-.3.7-.4 1-.2 1.1.4 2.300.6 3.6.6.6 0 1 .4 1 1V20c0 .6-.4 1-1 1C10.6 21 3 13.4 3 4c0-.6.4-1 1-1h3.5c.6 0 1 .4 1 1 0 1.3.2 2.5.6 3.6.1.3 0 .7-.2 1l-2.3 2.2z"/></svg>
        020 7946 0318
      </li>
      <li>
        <svg viewBox="0 0 24 24" aria-hidden="true"><path fill="#111" d="M2 6h20v13H2z"/><path fill="none" stroke="#fff" stroke-width="1.8" d="M2.5 7l9.5 7 9.5-7M2.5 18.5l7-6M21.5 18.5l-7-6"/></svg>
        info@gentlelinenlofts.com
      </li>
      <li>
        <svg viewBox="0 0 24 24" aria-hidden="true"><circle cx="12" cy="12" r="10" fill="#111"/><path fill="#fff" d="M7 6c2 0 3 1 3 2.5S8 10 8 11.5 10 13 10 15s-1 3-2 4c-2-1.5-4-4-4-7 0-2.5 1.2-4.6 3-6zM14 5c2 .5 4 2 4.5 4-1.5 0-2.5 1-3.5 1S13 8 14 5zM15 14c1.5 0 3 .5 3.5 1.5-.8 1.6-2 2.8-3.5 3.5-.5-1.5-1-3.5 0-5z"/></svg>
        www.gentlelinenlofts.com
      </li>
    </ul>

    <p class="address">Alder House, 42 Mill Lane, London N1 4QT</p>
  </main>
</body>
</html>
```